Application for baby milk and water counter

We are building baby food app. Need to design main screen for tha app first so we can go forward to other secondary screens of the app

Food dashboard screen
Food dashboard screen is main page for view/edit food data

General vision
I see the app in pastel colors with some illustrations to make the app more in positive. You can influence from game Glimmer Tides. I see with smooth colors and gradients like in a game. Also need to have animations/transitions for each action. Each click should create smooth transition to new state. My idea is to build one dashboard screen for food which we can reuse it for other screens. So a lot of thinking should go into design stage to app appealing.

Food Dashboard
Current screen should show all the data about food intake of the baby. So here user should see

Milk How much food baby had in ml/oz. So there should be some kind of illustrated bottle or glass or smth that shows it is filled with that amount.

Add/Remove controls for food. Should be some kind of custom control for inputing amount to remove/add. I see it as a slider on the side of the bottle. User slides up or down and amount is added/removed.

Notification. So user should be aware how many hours/minutes left for next food intake. This is optional field, so consider it could be disabled. So no empty space should be on a screen. There should be human readable text. Something like. 1:30 minutes left for next intake. Maybe could be some custom made icons to illustrate that it is next food intake.

Burped: User should have ability to how much baby burped. This amount is integer value. So it could be “Baby burped 2 times today”. So again here I see some custom made/icon to illustrate how many times baby burped and amount next to it. I see changing the value just by tapping, but I don’t know how to edit if user tapped accidentally more than it should be. So TBD here.

Date and time: Dashboard should show for which date it is viewing/editing data. Should be able to change it, so user can add/edit data for yesterday. Don’t want to see here calendar on a screen so need to come up with nice design decision.

Water: User should have ability to view/edit water intake of the baby, but water is secondary information so it should be smaller than milk, or come up with some other idea how to show the water. I see to have same controls for water like for milk. Water intake is optional it can be disabled by the user.

Target Market(s)

For just became mothers

Font styles to use
Sans Serif

Colors
0094D4
00A9DD
6FCCEA
C7EBF8
E9F6FB
FFC000
F8CF3A
FAE287
FDF2CF
FEFAEE
E54698
E96AAD
F1A4CE
F9D9EA
FCEFF6

Requirements
Must have
• Ilustrations or playfull icons for show information

```html
<!DOCTYPE html>
<html lang="en">
<head>
<meta charset="UTF-8">
<title>Baby Food Dashboard</title>
<link href="https://fonts.googleapis.com/css2?family=Federo&display=swap" rel="stylesheet">
<style>
  :root {
    --blue-deep: #0094D4;
    --blue: #00A9DD;
    --blue-soft: #6FCCEA;
    --blue-pale: #C7EBF8;
    --blue-mist: #E9F6FB;
    --yellow: #FFC000;
    --yellow-soft: #F8CF3A;
    --yellow-pale: #FAE287;
    --cream: #FDF2CF;
    --cream-light: #FEFAEE;
    --pink-deep: #E54698;
    --pink: #E96AAD;
    --pink-soft: #F1A4CE;
    --pink-pale: #F9D9EA;
    --pink-mist: #FCEFF6;
    --white: #FFFFFF;
    --ink: #2B2B2B;
  }
  * { margin: 0; padding: 0; box-sizing: border-box; }
  html, body { width: 1200px; height: 2560px; overflow: hidden; }
  body {
    font-family: "Federo", sans-serif;
    color: var(--ink);
    background: linear-gradient(180deg, var(--pink-deep) 0%, #B65DB0 40%, #5C7FCB 70%, var(--blue-deep) 100%);
    position: relative;
  }
  .screen {
    position: absolute;
    left: 32px; top: 38px;
    width: 1139px; height: 2458px;
    border-radius: 38px;
    overflow: hidden;
    background:
      radial-gradient(ellipse 420px 260px at 300px 1100px, rgba(255,255,255,0.55), transparent 70%),
      radial-gradient(ellipse 500px 300px at 850px 1500px, rgba(255,255,255,0.45), transparent 70%),
      radial-gradient(ellipse 460px 280px at 400px 2000px, rgba(255,255,255,0.5), transparent 70%),
      linear-gradient(180deg, var(--pink-pale) 0%, var(--pink-mist) 55%, var(--white) 100%);
  }
  .header-band { position: absolute; left: 0; top: 0; width: 1139px; height: 900px; }
  .abs { position: absolute; }

  .hero-art {
    left: 410px; top: 110px; width: 520px; height: 650px;
    border-radius: 260px 260px 220px 220px;
    background: linear-gradient(160deg, var(--cream-light) 0%, var(--cream) 30%, var(--yellow-pale) 60%, var(--yellow-soft) 100%);
  }
  .date-chip {
    left: 64px; top: 112px; width: 438px; height: 122px;
    background: var(--white);
    display: flex; align-items: center; gap: 44px;
    padding-left: 58px;
    font-size: 27px;
  }

  .intake-card {
    background: var(--white);
    box-shadow: 0 6px 18px rgba(229,70,152,0.08);
  }
  .milk-card { left: 198px; top: 1002px; width: 810px; height: 352px; border-radius: 24px 110px 110px 24px; }
  .water-card { left: 198px; top: 1411px; width: 810px; height: 349px; border-radius: 110px 24px 24px 110px; }

  .bottle-art { border-radius: 50px 50px 28px 28px; }
  .milk-bottle-art {
    left: 350px; top: 1040px; width: 130px; height: 272px;
    background: linear-gradient(180deg, var(--pink-soft) 0%, var(--yellow-pale) 28%, var(--cream) 55%, var(--cream-light) 100%);
  }
  .water-bottle-art {
    left: 784px; top: 1488px; width: 118px; height: 266px;
    background: linear-gradient(180deg, var(--yellow-pale) 0%, var(--blue-soft) 30%, var(--blue-pale) 60%, var(--cream) 100%);
  }
  .amount-line { height: 3px; background: var(--ink); }
  .amount-label { font-size: 26px; line-height: 30px; }

  .card-title { font-size: 48px; line-height: 88px; letter-spacing: 1px; font-weight: 400; }

  .burp-control {
    left: 272px; top: 1850px; width: 640px; height: 109px;
    border-radius: 55px;
    background: var(--white);
    display: flex; align-items: center; justify-content: space-between;
    padding: 0 26px;
  }
  .burp-label { font-size: 46px; letter-spacing: 1px; }
  .step-btn { width: 70px; height: 70px; }

  .baby-art {
    left: 56px; top: 2060px; width: 230px; height: 420px;
    border-radius: 115px 115px 60px 60px;
    background: linear-gradient(180deg, var(--cream) 0%, var(--yellow-pale) 40%, var(--blue-pale) 75%, var(--blue-mist) 100%);
  }
  .intake-alert {
    left: 390px; top: 2102px; width: 596px; height: 186px;
    background: var(--white);
    display: flex; align-items: center; justify-content: center;
    padding-left: 70px; padding-right: 24px;
    text-align: center;
    font-size: 34px; line-height: 50px;
  }
  .alert-icon { left: 345px; top: 2150px; width: 90px; height: 90px; }
</style>
</head>
<body>
  <main class="screen">
    <svg class="header-band" viewBox="0 0 1139 900" aria-hidden="true">
      <path d="M0 0 H1139 V730 Q569.5 890 0 730 Z" fill="var(--blue-deep)"/>
    </svg>
  </main>

  <div class="abs hero-art" role="img" aria-label="Illustration of a sleeping baby in a striped night cap resting on a yellow crescent moon"></div>

  <div class="abs date-chip">
    <svg width="100" height="96" viewBox="0 0 100 96" aria-hidden="true">
      <rect x="4" y="12" width="92" height="80" rx="10" fill="#EDEDED" stroke="#9A9A9A" stroke-width="3"/>
      <rect x="4" y="12" width="92" height="22" rx="10" fill="#E84A4A"/>
      <rect x="22" y="2" width="8" height="20" rx="4" fill="#666"/>
      <rect x="70" y="2" width="8" height="20" rx="4" fill="#666"/>
      <g fill="#9A9A9A">
        <rect x="16" y="44" width="12" height="9"/><rect x="34" y="44" width="12" height="9"/><rect x="52" y="44" width="12" height="9"/><rect x="70" y="44" width="12" height="9"/>
        <rect x="16" y="59" width="12" height="9"/><rect x="34" y="59" width="12" height="9"/><rect x="52" y="59" width="12" height="9"/><rect x="70" y="59" width="12" height="9"/>
        <rect x="16" y="74" width="12" height="9"/><rect x="34" y="74" width="12" height="9"/><rect x="52" y="74" width="12" height="9"/>
      </g>
    </svg>
    <span class="date-text">25/04/2023</span>
  </div>

  <section class="abs intake-card milk-card"></section>
  <div class="abs bottle-art milk-bottle-art" role="img" aria-label="Illustration of a milk bottle with a pink teat, filled with milk"></div>
  <div class="abs amount-line" style="left:384px; top:1199px; width:154px;"></div>
  <span class="abs amount-label" style="left:547px; top:1185px;">100ML</span>
  <h2 class="abs card-title" style="left:744px; top:1092px;">MILK<br>BOTTLE</h2>

  <section class="abs intake-card water-card"></section>
  <h2 class="abs card-title" style="left:307px; top:1504px;">WATER<br>BOTTLE</h2>
  <span class="abs amount-label" style="left:614px; top:1595px;">50ML</span>
  <div class="abs amount-line" style="left:684px; top:1609px; width:150px;"></div>
  <div class="abs bottle-art water-bottle-art" role="img" aria-label="Illustration of a blue water bottle, partly filled"></div>

  <div class="abs burp-control">
    <svg class="step-btn" viewBox="0 0 70 70" role="img" aria-label="Add burp">
      <circle cx="35" cy="35" r="35" fill="var(--blue-deep)"/>
      <rect x="19" y="32" width="32" height="6" rx="3" fill="var(--white)"/>
      <rect x="32" y="19" width="6" height="32" rx="3" fill="var(--white)"/>
    </svg>
    <span class="burp-label">BABY BURPED</span>
    <svg class="step-btn" viewBox="0 0 70 70" role="img" aria-label="Remove burp">
      <circle cx="35" cy="35" r="35" fill="var(--blue-deep)"/>
      <rect x="19" y="32" width="32" height="6" rx="3" fill="var(--white)"/>
    </svg>
  </div>

  <div class="abs baby-art" role="img" aria-label="Illustration of a crying baby in a bib and blue diaper"></div>

  <div class="abs intake-alert">2 HOURS LEFT FOR NEXT INTAKE</div>
  <svg class="abs alert-icon" viewBox="0 0 90 90" aria-hidden="true">
    <defs>
      <linearGradient id="ringGrad" x1="0" y1="0" x2="1" y2="1">
        <stop offset="0" stop-color="#0094D4"/>
        <stop offset="1" stop-color="#E54698"/>
      </linearGradient>
    </defs>
    <circle cx="45" cy="45" r="40" fill="#FFFFFF" stroke="url(#ringGrad)" stroke-width="4"/>
    <path d="M45 24 C34 24 30 33 30 42 V52 L25 59 H65 L60 52 V42 C60 33 56 24 45 24 Z" fill="none" stroke="url(#ringGrad)" stroke-width="4" stroke-linejoin="round"/>
    <path d="M39 63 Q45 70 51 63" fill="none" stroke="url(#ringGrad)" stroke-width="4" stroke-linecap="round"/>
  </svg>
</body>
</html>
```